Marwick Law Letterhead

We need a new letterhead design for a Law Firm. The address for the law firm is 1475 Calloway Street, Suite 210, Houston, Texas 77041. Phone Number: 832-361-9027; Fax Number: 832-614-7359. The logo is uploaded to the project.

```html
<!DOCTYPE html>
<html lang="en">
<head>
<meta charset="utf-8">
<title>Marwick Law Letterhead</title>
<link href="https://fonts.googleapis.com/css2?family=Montserrat:wght@400;500;600&family=Cormorant+Garamond:wght@600&display=swap" rel="stylesheet">
<style>
  :root {
    --backdrop: #e6e6e8;
    --paper: #ffffff;
    --navy: #1f2a5c;
    --red: #d0141f;
    --red-deep: #9e0d18;
    --ink: #1b1b1b;
    --band-text: #ffffff;
  }
  html, body {
    margin: 0;
    width: 1200px;
    height: 960px;
    overflow: hidden;
    background: var(--backdrop);
  }
  .letterhead {
    position: absolute;
    left: 282px;
    top: 30px;
    width: 636px;
    height: 900px;
    background: var(--paper);
    box-shadow: 0 8px 24px rgba(0,0,0,0.12);
    font-family: "Montserrat", sans-serif;
    color: var(--ink);
  }
  .brand {
    position: absolute;
    left: 46px;
    top: 48px;
    display: flex;
    align-items: center;
    gap: 12px;
  }
  .brand-dot {
    width: 34px;
    height: 34px;
    border-radius: 50%;
    background: var(--navy);
  }
  .brand-name {
    font-family: "Cormorant Garamond", serif;
    font-weight: 600;
    font-size: 30px;
    letter-spacing: 1px;
    color: var(--navy);
  }
  .contact-band {
    position: absolute;
    left: 0;
    right: 0;
    top: 118px;
    height: 36px;
    background: linear-gradient(90deg, var(--red) 0%, var(--red-deep) 100%);
    display: flex;
    align-items: center;
    padding-left: 138px;
    gap: 14px;
    color: var(--band-text);
    font-size: 11px;
    font-weight: 500;
  }
  .contact-item { display: flex; align-items: center; gap: 5px; white-space: nowrap; }
  .contact-item svg { width: 11px; height: 11px; fill: var(--band-text); }
  .letter-body {
    position: absolute;
    left: 138px;
    right: 50px;
    top: 188px;
    font-size: 10.5px;
    line-height: 1.45;
  }
  .recipient { margin: 0 0 4px; }
  .recipient span { display: block; }
  .recipient span:nth-child(2) { padding-left: 12px; }
  .recipient span:nth-child(3) { padding-left: 24px; }
  .recipient span:nth-child(4) { padding-left: 36px; }
  .letter-body p.paragraph { margin: 0 0 22px; padding-left: 46px; }
  .closing { padding-left: 46px; margin-top: 22px; font-size: 12px; }
  .signature {
    margin: 8px 0 0 60px;
    width: 90px;
    height: 34px;
    background: linear-gradient(90deg, #f1f1f1, #e2e2e2);
    border-radius: 3px;
  }
</style>
</head>
<body>
  <main class="letterhead">
    <header class="brand">
      <span class="brand-dot"></span>
      <span class="brand-name">Marwick Law</span>
    </header>

    <div class="contact-band">
      <span class="contact-item">1475 Calloway Street, Suite 210, Houston, Texas 77041</span>
      <span class="contact-item">
        <svg viewBox="0 0 24 24" aria-hidden="true"><path d="M6.6 10.8a15.1 15.1 0 0 0 6.6 6.6l2.2-2.2a1 1 0 0 1 1-.25 11.4 11.4 0 0 0 3.6.57 1 1 0 0 1 1 1V20a1 1 0 0 1-1 1A17 17 0 0 1 3 4a1 1 0 0 1 1-1h3.5a1 1 0 0 1 1 1c0 1.25.2 2.45.57 3.6a1 1 0 0 1-.25 1z"/></svg>
        832-361-9027
      </span>
      <span class="contact-item">
        <svg viewBox="0 0 24 24" aria-hidden="true"><path d="M6 2h12v6H6zM4 9h16a2 2 0 0 1 2 2v6h-4v5H6v-5H2v-6a2 2 0 0 1 2-2zm4 8v3h8v-3z"/></svg>
        832-614-7359
      </span>
    </div>

    <section class="letter-body">
      <p class="recipient">
        <span>Mr/s</span>
        <span>First Name and Last Name</span>
        <span>Company Name</span>
        <span>Address</span>
      </p>
      <p class="paragraph">Lorem ipsum dolor sit amet,consectetur adipiscing sed do eiusmod tempor incididunt laboreet dolore magna aliqua.Ut enim ad minim.veniam, quis nostrud exercitation ullamco laboris nisi ut aliquip exea commodo consequat.Lorem ipsum dolor sit amet,consectetur adipiscing sed do eiusmod tempor incididunt.labore et dolore magna aliqua. Ut enim</p>
      <p class="paragraph">Lorem ipsum dolor sit amet, consectetur adipiscing sed do eiusmod tempor incididunt labore et dolore magna aliqua. Ut enim ad minim veniam, quis nostrud exercitation ullamco laboris nisi ut aliquip exea commodo consequat.Duis aute irure dolor in reprehenderit in voluptate velit esse cillum irure dolor in reprehenderit in voluptate velit esse irure</p>
      <p class="paragraph">Lorem ipsum dolor sit amet, consectetur adipiscing sed do eiusmod tempor incididunt labore et dolore magna aliqua. consequat. Duis aute irure dolor in:reprehenderit in voluptate velit esse cillum dolore eu fugiat nulla pariatur. Excepteur sint occaecat cupidatat non proident, sunt in culpa qui officia deserunt mollit,</p>
      <p class="paragraph">Lorem ipsum dolor sit amet, consectetur adipiscing sed do eiusmod tempor incididunt labore et dolore magna aliqua. Ut enim Lorem ipsum dolor sit amet, consectetur adipiscing sed do eiusmod tempor incididunt labore et dolore magna aliqua. Ut enim Lorem ipsum aliqua.ipsum</p>
      <p class="paragraph">Lorem ipsum dolor sit amet, consectetur adipiscing sed do eiusmod tempor incididunt labore et dolore magna aliqua. Ut enim ad minim veniam, quis nostrud exercitation ullamco laboris nisi ut aliquip exea commodo consequat.Duis aute irure dolor in reprehenderit in voluptate velit esse cillum irure dolor in reprehenderit in voluptate velit esse irure</p>
      <div class="closing">
        Regards
        <div class="signature" role="img" aria-label="Handwritten signature of Hallowell"></div>
      </div>
    </section>
  </main>
</body>
</html>
```